Brightbay Orthodontics business card design

Need a business card design that reflects our re-branding (orthodontic office - braces) and a new partnership with a pediatric dental office. We would like to include "for adults and children" on the card as well so adults know they are welcome to get their braces here as well. Office design is modern and would like business card to reflect a modern type look. Here's the text we would like to be included on the card:

Darren Wolcott, DDS, MSD
5214 West Linden Avenue, Suite 204
Mansfield, TX 76991
555-418-2637
www.brightbayortho.example
info@brightbayortho.example

Can we add the following to the existing designs? Darren Wolcott, DDS, MSD 5214 West Linden Avenue, Suite 204 Mansfield, TX 76991 555-418-2637

Does anyone have any more vertical designs available? Thanks!

Dental

```html
<!DOCTYPE html>
<html lang="en">
<head>
<meta charset="utf-8">
<title>Brightbay Orthodontics – Business Card</title>
<link rel="stylesheet" href="https://fonts.googleapis.com/css2?family=Ubuntu:wght@400;500;700&display=swap">
<style>
  :root {
    --backdrop: #e9e6e1;
    --card: #ffffff;
    --ink: #1a1a1a;
    --name-blue: #1d72b8;
    --tag-green: #8cc63f;
    --accent-orange: #f7941d;
    --accent-pink: #ec1c8c;
    --base-black: #111111;
    --brand-dot: #f7941d;
  }
  * { box-sizing: border-box; margin: 0; padding: 0; }
  html, body {
    width: 1200px; height: 1023px; overflow: hidden;
    background: var(--backdrop);
    font-family: "Ubuntu", sans-serif;
    color: var(--ink);
  }
  .business-card {
    position: absolute; left: 360px; top: 72px;
    width: 480px; height: 880px;
    background: var(--card);
    border-radius: 10px;
    overflow: hidden;
    box-shadow: 0 12px 30px rgba(0,0,0,.18);
    text-align: center;
  }
  .brand {
    margin-top: 90px;
    display: flex; align-items: center; justify-content: center; gap: 14px;
  }
  .brand-dot {
    width: 26px; height: 26px; border-radius: 50%;
    background: var(--brand-dot);
    flex: none;
  }
  .brand-name {
    font-weight: 700; font-size: 34px; line-height: 1.05;
    color: var(--ink); text-align: left;
  }
  .tagline {
    margin-top: 12px;
    font-size: 20px; font-weight: 500; color: var(--tag-green);
  }
  .doctor-name {
    margin-top: 44px;
    font-size: 30px; font-weight: 500; color: var(--name-blue);
  }
  .credentials { margin-top: 4px; font-size: 19px; font-weight: 500; }
  .address {
    margin-top: 44px; font-size: 20px; font-weight: 500; line-height: 1.35;
  }
  .contact-list {
    list-style: none; margin-top: 40px;
    display: inline-flex; flex-direction: column; gap: 8px; text-align: left;
    font-size: 20px; font-weight: 500;
  }
  .contact-list li { display: flex; align-items: center; gap: 10px; }
  .contact-icon { width: 20px; height: 20px; flex: none; }
  .footer-decoration {
    position: absolute; left: 0; bottom: 0;
    width: 480px; height: 160px;
    background: linear-gradient(180deg, var(--accent-orange) 0%, var(--accent-pink) 40%, var(--base-black) 85%);
  }
</style>
</head>
<body>
  <section class="business-card">
    <header class="brand">
      <span class="brand-dot"></span>
      <span class="brand-name">Brightbay<br>Orthodontics</span>
    </header>
    <p class="tagline">For Adults and Children</p>

    <h1 class="doctor-name">Darren Wolcott</h1>
    <p class="credentials">DDS, MSD</p>

    <p class="address">5214 West Linden Avenue,<br>Suite 204 Mansfield,<br>TX 76991</p>

    <ul class="contact-list">
      <li>
        <svg class="contact-icon" viewBox="0 0 20 20" aria-hidden="true">
          <rect x="5" y="1.5" width="10" height="17" rx="2" fill="none" stroke="#ec1c8c" stroke-width="2"/>
          <rect x="8" y="15" width="4" height="1.5" fill="#ec1c8c"/>
        </svg>
        555-418-2637
      </li>
      <li>
        <svg class="contact-icon" viewBox="0 0 20 20" aria-hidden="true">
          <rect x="1" y="4" width="18" height="12" fill="#8cc63f"/>
          <path d="M1 4 L10 11 L19 4" fill="none" stroke="#fff" stroke-width="1.5"/>
        </svg>
        info@brightbayortho.example
      </li>
      <li>
        <svg class="contact-icon" viewBox="0 0 20 20" aria-hidden="true">
          <circle cx="10" cy="10" r="8.5" fill="#f7941d"/>
          <ellipse cx="10" cy="10" rx="3.5" ry="8.5" fill="none" stroke="#fff" stroke-width="1.2"/>
          <line x1="1.5" y1="10" x2="18.5" y2="10" stroke="#fff" stroke-width="1.2"/>
        </svg>
        www.brightbayortho.example
      </li>
    </ul>

    <div class="footer-decoration" role="img" aria-label="Decorative curved colour bands in orange, green, pink and black along the bottom of the card"></div>
  </section>
</body>
</html>
```